Card Design Project

We are looking for a couple card / box designs that will for a new company that is in the bereavement assistance industry.
Our customers are churches, counseling centers and funeral homes.
Once we have these card designs we will need to work with that same artist to help us out with box graphic designs that are similar to the card designs. The box is 12" long x 4" wide x 6" high
We will need more designs in the future so we are looking for an artist for future work.
Our look needs to be professional and solemn.
The front of the card should be quite close to what i am attaching but with some professional touches to it that give it a proper look. We dont want you to stray to far from what i have attached but if you feel you have some good ideas we would be more than happy to see them.
The back of the card we want people to be able to leave the family a note so will need wording such as "leave a message to the family" or "write a memory"
Keep in mind we will need this look to be able to match graphics on the box as well, we kind of need the card design and box design to go together.
Thanks
Just wanted to mention to all designers that although we would like our logo on the card it is something that we need to keep kind of in the background somehow. We cant be seen as trying to push a brand name too much so please keep that in mind. Thanks
Designers, I took the need to see what the design looked like on a box out.
Target Market(s)
Funeral homes, churches, counseling centers
Industry/Entity Type
Industry
Requirements
Must have
- Professional and solemn look
Card need to be 4"wide X 6" high and needs to be portrait
A pin will be attached to the top right part of the card so will need a space there for it.
I was thinking that we would have the pic of the ribbon symbol there so when the pin is off the card there would still be a ribbon pic there. The pins that we will be attaching are ribbon pins similar to what i have on my pdf's
Please keep in mind that we cant really have out logo in a dominant area on the card. We would like to have it subtly in there but not to where it is in your face type of thing.
Nice to have
- Our logo but very small, not to intrusive .
Would like 2 designs, one dark and another light.
Maybe 1 masculine or gender neutral and another feminine
Wording should be the same

```html
<!DOCTYPE html>
<html lang="en">
<head>
<meta charset="utf-8">
<title>Memorial Card – Dark Front and Memory Back</title>
<link rel="stylesheet" href="https://fonts.googleapis.com/css2?family=Almendra&family=Arimo&display=swap">
<style>
  :root {
    --page: #ffffff;
    --card-dark: #000000;
    --ink-light: #ffffff;
    --ink-dark: #1a1a1a;
    --rule-dark: #8a8a8a;
    --rule-light: #7a7a7a;
    --ribbon-hi: #6e6e6e;
    --ribbon-lo: #2e2e2e;
    --ornament-hi: rgba(255,255,255,0.9);
    --ornament-lo: rgba(255,255,255,0.55);
  }
  * { margin: 0; padding: 0; box-sizing: border-box; }
  html, body { width: 1200px; height: 856px; overflow: hidden; background: var(--page); }
  .canvas { position: relative; width: 1200px; height: 856px; }

  /* Front card */
  .card-front {
    position: absolute; left: 6px; top: 10px; width: 547px; height: 822px;
    background: var(--card-dark);
  }
  .frame {
    position: absolute; left: 28px; top: 51px; width: 491px; height: 726px;
    border: 3px solid var(--ink-light);
  }
  .flourish {
    position: absolute; height: 44px; border-radius: 22px;
    background: linear-gradient(90deg, var(--ornament-lo), var(--ornament-hi), var(--ornament-lo));
    border: 6px solid var(--card-dark);
  }
  .flourish--top { left: 58px; top: 10px; width: 436px; }
  .flourish--bottom { left: 52px; top: 758px; width: 446px; }
  .ribbon {
    position: absolute; left: 402px; top: 72px; width: 114px; height: 124px;
    border-radius: 50% 50% 20% 20%;
    background: linear-gradient(160deg, var(--ribbon-hi), var(--ribbon-lo));
  }
  .greeting {
    position: absolute; left: 0; width: 547px; top: 140px; padding-left: 0;
    text-align: center; font-family: "Almendra", serif; font-size: 38px;
    color: var(--ink-light); letter-spacing: 1px;
  }
  .message {
    position: absolute; left: 0; width: 547px; text-align: center;
    font-family: "Arimo", Arial, sans-serif; font-size: 19.5px; line-height: 34px;
    color: var(--ink-light);
  }
  .message--support { top: 254px; }
  .message--touched { top: 357px; }
  .message--pin { top: 459px; }
  .message--thanks { top: 664px; }
  .divider {
    position: absolute; left: 78px; width: 421px; height: 2px; background: var(--rule-dark);
  }
  .divider__mark {
    position: absolute; left: 172px; top: -9px; width: 76px; height: 20px;
    background: var(--card-dark);
  }
  .divider__mark span {
    position: absolute; left: 6px; top: 3px; width: 64px; height: 14px; border-radius: 7px;
    background: var(--ornament-hi);
  }
  .divider--one { top: 337px; }
  .divider--two { top: 443px; }
  .divider--three { top: 631px; }

  /* Back card */
  .card-back {
    position: absolute; left: 643px; top: 18px; width: 549px; height: 821px;
    border: 1.5px solid var(--ink-dark); background: var(--page);
  }
  .memory-title {
    position: absolute; left: 42px; top: 208px; font-family: "Almendra", serif;
    font-size: 24px; color: var(--ink-dark); letter-spacing: 0.5px;
  }
  .memory-title-rule {
    position: absolute; left: 253px; top: 228px; width: 265px; height: 1px; background: var(--rule-light);
  }
  .memory-lines { position: absolute; left: 38px; top: 260px; width: 480px; }
  .memory-lines li {
    list-style: none; height: 32.4px; border-bottom: 1px solid var(--rule-light);
  }
</style>
</head>
<body>
<main class="canvas">
  <section class="card-front">
    <div class="frame"></div>
    <div class="flourish flourish--top" role="img" aria-label="Decorative white scroll flourish"></div>
    <div class="flourish flourish--bottom" role="img" aria-label="Decorative white scroll flourish"></div>
    <div class="ribbon" role="img" aria-label="Grey awareness ribbon, space for the ribbon pin"></div>

    <h1 class="greeting">Dear Friends</h1>

    <p class="message message--support">Your support in attending this memorial<br>and celebration of life means so much to us.</p>
    <div class="divider divider--one"><div class="divider__mark"><span role="img" aria-label="Small scroll ornament"></span></div></div>

    <p class="message message--touched">Our loved one has touched you in ways<br>we may not even recognize yet.</p>
    <div class="divider divider--two"><div class="divider__mark"><span role="img" aria-label="Small scroll ornament"></span></div></div>

    <p class="message message--pin">We invite you to wear this pin through<br>your grieving process, which we receive as<br>a symbol of your sympathy and support<br>of our loss.</p>
    <div class="divider divider--three"><div class="divider__mark"><span role="img" aria-label="Small scroll ornament"></span></div></div>

    <p class="message message--thanks">Thank you for grieving together with us</p>
  </section>

  <section class="card-back">
    <h2 class="memory-title">Write a memory</h2>
    <div class="memory-title-rule"></div>
    <ul class="memory-lines">
      <li></li><li></li><li></li><li></li><li></li><li></li><li></li>
      <li></li><li></li><li></li><li></li><li></li><li></li><li></li>
    </ul>
  </section>
</main>
</body>
</html>
```